Summit Ridge Business Card

Side 1: Summit Ridge Logo (logo without Maltese cross) with industrial rope rescue related theme. Our company services - TRAINING - Fire Training, Confined Space Rescue Training, Rope Rescue training, Hazmat Training, Incident Command, EMS, Pump Operations Training. Website - summitridgeexample.com.
Side 2: Summit Ridge Fire Department Logo (logo with Maltese cross) with Firefighter related theme. Company (division) services - FIELD SERVICES - Fire Department, Stand-by Rescue, Safety, EMS, Planning. "Supporting the Emergency Response Community Since 1967"

Add contact information wherever it makes since (Name, Email, Phone).
I would like it to represent the Summit Ridge Fire Department Logo as a division not as a separate entity without saying it, possibly by depicting it in the background of Side 2 instead of being a standalone picture like the logo on Side 1.

```html
<!DOCTYPE html>
<html lang="en">
<head>
<meta charset="utf-8">
<title>Summit Ridge Business Card</title>
<link rel="stylesheet" href="https://fonts.googleapis.com/css2?family=Arimo:wght@400;700&display=swap">
<style>
  :root {
    --ink: #141414;
    --paper: #ffffff;
    --accent: #e8402a;
    --backdrop: #d9d9d9;
    --muted: #cfcfcf;
  }
  * { margin: 0; padding: 0; box-sizing: border-box; }
  html, body {
    width: 1200px; height: 863px; overflow: hidden;
    background: var(--backdrop);
    font-family: "Arimo", Arial, sans-serif;
  }
  .sheet {
    width: 1200px; height: 863px;
    display: flex; flex-direction: column; align-items: center; justify-content: center;
    gap: 48px;
  }
  .card {
    position: relative; width: 640px; height: 366px;
    background: var(--paper); overflow: hidden;
    box-shadow: 0 6px 18px rgba(0,0,0,.18);
  }
  .card-shape { position: absolute; inset: 0; }
  .abs { position: absolute; }

  /* Training side */
  .brand-training {
    left: 300px; top: 82px; width: 200px; text-align: center;
    color: var(--accent); font-weight: 700; font-size: 26px; letter-spacing: 2px;
    display: flex; align-items: center; justify-content: center; gap: 10px;
  }
  .brand-mark { width: 14px; height: 14px; background: var(--accent); flex: none; }
  .section-title { color: var(--accent); font-weight: 700; font-size: 21px; letter-spacing: .5px; }
  .service-list { list-style: none; color: var(--ink); font-size: 15.5px; line-height: 19px; }
  .service-list li { display: flex; align-items: center; gap: 9px; }
  .service-list li::before {
    content: ""; width: 7px; height: 7px; background: var(--accent); flex: none;
  }
  .training-title { left: 40px; top: 142px; }
  .training-list { left: 40px; top: 172px; }
  .training-list-more { left: 400px; top: 236px; }
  .website {
    left: 0; right: 0; top: 312px;
    display: flex; align-items: center; justify-content: center; gap: 14px;
    color: var(--ink); font-size: 18px;
  }
  .website .rule { width: 72px; height: 2px; background: var(--accent); }

  /* Field services side */
  .brand-field {
    left: 40px; top: 70px;
    display: flex; align-items: center; gap: 14px;
    color: var(--ink); font-weight: 700; font-size: 30px; letter-spacing: 3px;
  }
  .brand-field .brand-mark { width: 20px; height: 20px; }
  .tagline { left: 330px; top: 40px; width: 290px; font-size: 9.5px; font-weight: 700; color: var(--ink); text-align: right; }
  .field-title { left: 470px; top: 140px; font-size: 17px; }
  .field-list { left: 470px; top: 164px; font-size: 14px; line-height: 17px; }
  .person { left: 40px; top: 232px; }
  .person-name { font-size: 24px; color: var(--paper); }
  .person-name .first { color: var(--accent); }
  .person-role { font-size: 13px; color: var(--muted); margin-top: 4px; text-align: right; }
  .divider { left: 296px; top: 232px; width: 2px; height: 56px; background: var(--accent); }
  .contact { left: 330px; top: 286px; list-style: none; color: var(--paper); font-size: 16.5px; line-height: 24px; }
  .contact li { display: flex; align-items: center; gap: 10px; }
  .contact svg { width: 12px; height: 12px; flex: none; }
</style>
</head>
<body>
<main class="sheet">

  <section class="card card-training" aria-label="Training side">
    <svg class="card-shape" viewBox="0 0 640 366" aria-hidden="true">
      <path d="M0,0 H640 V212 C560,236 470,200 380,168 C290,136 210,96 130,104 C70,110 30,126 0,138 Z" fill="var(--ink)"/>
      <path d="M0,138 C30,126 70,110 130,104 C210,96 290,136 380,168 C470,200 560,236 640,212" fill="none" stroke="var(--accent)" stroke-width="3"/>
    </svg>
    <div class="abs brand-training"><span class="brand-mark"></span>SUMMIT RIDGE</div>
    <h2 class="abs section-title training-title">TRAINING</h2>
    <ul class="abs service-list training-list">
      <li>Fire Training</li>
      <li>Confined Space Rescue Training</li>
      <li>Rope Rescue Training</li>
      <li>Hazmat Training</li>
    </ul>
    <ul class="abs service-list training-list-more">
      <li>Incident Command</li>
      <li>EMS</li>
      <li>Pump Operations Training</li>
    </ul>
    <div class="abs website"><span class="rule"></span>www.summitridgeexample.com<span class="rule"></span></div>
  </section>

  <section class="card card-field" aria-label="Field services side">
    <svg class="card-shape" viewBox="0 0 640 366" aria-hidden="true">
      <path d="M0,176 C150,150 260,200 360,256 C450,304 560,302 640,270 V366 H0 Z" fill="var(--ink)"/>
      <path d="M0,176 C150,150 260,200 360,256 C450,304 560,302 640,270" fill="none" stroke="var(--accent)" stroke-width="3"/>
    </svg>
    <div class="abs brand-field"><span class="brand-mark"></span>SUMMIT RIDGE</div>
    <p class="abs tagline">Supporting the Emergency Response Community Since 1967</p>
    <h2 class="abs section-title field-title">FIELD SERVICES</h2>
    <ul class="abs service-list field-list">
      <li>Fire Department</li>
      <li>Stand-by Rescue</li>
      <li>Safety</li>
      <li>EMS</li>
      <li>Planning</li>
    </ul>
    <div class="abs person">
      <p class="person-name"><span class="first">Daniel</span> Brooks</p>
      <p class="person-role">Director</p>
    </div>
    <div class="abs divider"></div>
    <ul class="abs contact">
      <li>
        <svg viewBox="0 0 12 12" aria-hidden="true"><path d="M3,1 L5,3.5 L4,5 C4.6,6.4 5.6,7.4 7,8 L8.5,7 L11,9 L10,11 C5.5,11 1,6.5 1,2 Z" fill="var(--accent)"/></svg>
        (555) 018 2417
      </li>
      <li>
        <svg viewBox="0 0 12 12" aria-hidden="true"><rect x="0.5" y="2" width="11" height="8" fill="var(--accent)"/><path d="M0.5,2 L6,6.5 L11.5,2" fill="none" stroke="var(--ink)" stroke-width="1"/></svg>
        hello@summitridgeexample.com
      </li>
    </ul>
  </section>

</main>
</body>
</html>
```